Business Card Design

We are a commercial real estate brokerage in San Francisco, leasing office buildings downtown.
I would like a clean, elegant look. Simple but powerful .

Industry/Entity Type

Business

Contact Information for Business Card

Derek Holloway
lic# 07258143
415.555.0172
derek@velt-commercial.example
velt-commercial.example

```html
<!DOCTYPE html>
<html lang="en">
<head>
<meta charset="utf-8">
<title>Velt Commercial – Business Card</title>
<link rel="stylesheet" href="https://fonts.googleapis.com/css2?family=Jost:wght@600&family=Open+Sans:wght@400;600&display=swap">
<style>
  :root {
    --bg: #eceae6;
    --slate: #7587a3;
    --white: #ffffff;
    --paper: #f4f4f4;
    --grey: #6f6f6f;
    --ink: #3c3c3c;
  }
  * { box-sizing: border-box; margin: 0; padding: 0; }
  html, body { width: 1200px; height: 900px; overflow: hidden; }
  body {
    background: var(--bg);
    font-family: "Open Sans", Arial, sans-serif;
    position: relative;
  }
  .card {
    position: absolute;
    width: 520px;
    height: 300px;
    box-shadow: 0 10px 24px rgba(0,0,0,0.18);
    overflow: hidden;
  }
  .card-back {
    left: 60px; top: 110px;
    background: var(--slate);
    display: flex; align-items: center; justify-content: center;
  }
  .card-front {
    left: 620px; top: 490px;
    background: linear-gradient(#ffffff, var(--paper));
  }
  .wordmark {
    display: flex; align-items: center; gap: 14px;
    font-family: "Jost", "Futura", sans-serif;
    font-weight: 600;
    line-height: 0.95;
  }
  .wordmark .mark-square {
    width: 34px; height: 34px;
  }
  .wordmark .name-main { font-size: 52px; letter-spacing: 1px; display: block; }
  .wordmark .name-sub { font-size: 22px; letter-spacing: 1px; display: block; }
  .card-back .wordmark { color: var(--white); }
  .card-back .mark-square { background: var(--white); }
  .card-front .wordmark {
    position: absolute; left: 0; right: 0; top: 34px;
    justify-content: center;
    color: var(--slate);
  }
  .card-front .mark-square { background: var(--slate); }
  .front-rule {
    position: absolute; left: 0; right: 0; top: 148px;
    height: 10px; background: var(--grey);
  }
  .front-panel {
    position: absolute; left: 0; right: 0; top: 162px; bottom: 0;
    background: var(--slate);
    color: var(--white);
    display: flex; align-items: center;
    padding: 0 30px 0 40px;
  }
  .agent { flex: 1; text-align: right; padding-right: 34px; }
  .agent-name { font-size: 21px; font-weight: 600; }
  .agent-licence { font-size: 16px; font-weight: 600; margin-top: 2px; }
  .contacts { list-style: none; font-size: 13px; }
  .contacts li { display: flex; align-items: center; gap: 8px; margin: 5px 0; }
  .contacts svg { width: 12px; height: 12px; fill: var(--white); flex: none; }
</style>
</head>
<body>
  <section class="card card-back">
    <div class="wordmark">
      <span class="mark-square"></span>
      <span><span class="name-main">VELT</span><span class="name-sub">COMMERCIAL</span></span>
    </div>
  </section>

  <section class="card card-front">
    <div class="wordmark">
      <span class="mark-square"></span>
      <span><span class="name-main">VELT</span><span class="name-sub">COMMERCIAL</span></span>
    </div>
    <div class="front-rule"></div>
    <div class="front-panel">
      <div class="agent">
        <p class="agent-name">Derek Holloway</p>
        <p class="agent-licence">Lic# 07258143</p>
      </div>
      <ul class="contacts">
        <li><svg viewBox="0 0 24 24"><path d="M6.6 10.8a15.1 15.1 0 0 0 6.6 6.6l2.2-2.2a1 1 0 0 1 1-.25 11.4 11.4 0 0 0 3.6.57 1 1 0 0 1 1 1V20a1 1 0 0 1-1 1A17 17 0 0 1 3 4a1 1 0 0 1 1-1h3.5a1 1 0 0 1 1 1c0 1.25.2 2.45.57 3.57a1 1 0 0 1-.25 1z"/></svg>415.555.0172</li>
        <li><svg viewBox="0 0 24 24"><path d="M2 5h20v14H2z M2 5l10 8 10-8" /></svg>derek@velt-commercial.example</li>
        <li><svg viewBox="0 0 24 24"><path d="M10 14a4 4 0 0 1 0-5.6l3-3a4 4 0 0 1 5.6 5.6l-1.5 1.5-1.4-1.4 1.5-1.5a2 2 0 0 0-2.8-2.8l-3 3a2 2 0 0 0 0 2.8zm4-4a4 4 0 0 1 0 5.6l-3 3a4 4 0 0 1-5.6-5.6l1.5-1.5 1.4 1.4-1.5 1.5a2 2 0 0 0 2.8 2.8l3-3a2 2 0 0 0 0-2.8z"/></svg>velt-commercial.example</li>
      </ul>
    </div>
  </section>
</body>
</html>
```